Sunvale Bridal Atelier/ Wayfarer Escapes Global & Co- A one stop shop selling bridal g

Our Mission: to open a one stop shop for the bride & groom to make everything simple for the bride at this stressful time in her life to take a lot of the burden of the bride for she can enjoy the processed of getting marry. The bride will be assign a consultant that will keep in touch with her for 24 months, for the wedding and the first year anniversary.

Sunvale Bridal Atelier, will sell bridal gowns, jewelry, shoes party favors. If she has a wedding gown -that she loves we will find a way to make that dream come true and make the bride feel confident and happy through the process. Flower girls, bridesmaids, mother of the bride. And tuxedo rental for the groom with a cigar room….
Wayfarer Escapes Global & Co: is another part of the company the one stop shop experience that we will be offering the couples a travel agency & wedding consultant. If the couple is looking to do a destination wedding or honeymoon destination we can make the plans and work with the resort by confence call. Family vacation, anniversary, birthday, Pembrook trips cruises, party rental, limousine rental
Café des pins: will create a unique restaurant where the bride and wedding party can sit and eat after their fitting for the dresses, featuring Chef Tarik creation and offering catering. Cake testing from different bakery, wine, coffee specialties drinks, a romantic restantant for couple at night time feature cigar room, wine bar party room
Our Team: we our a full service bridal consulting group and our goal is to put the fun back into planning a wedding, holy union or anniversary to many people become frustrated when planning these wonderful events, with our experienced and professional consultants and will our expertise to help create memorable and stress-free events for our customers, by doing this, our clients can sit back and enjoy their events.
Our dedication: our consultant are experienced and dedicated processioned with many years of experiences, Sunvale Bridal Atelier couture bridal gowns is a unique in that we give our clients undivided attentions, we listen to their needs and work with them to crate the event of their dreams. Our clients wishes become our command. So , whether our clients want a western, tropical, Las Vegas, European or more traditional wedding we can help.
Our product: weddings gowns, tuxedo rental, flower girls dress, shoes, lingerie, mother of the bride dresses, Ostrow Noir, Beatriz Montalvo, Kivory, Celeste Dufresne, Lorna Fitch, Rosalind , Ilsa Vantorek, Fenella Atelier, Hugo Brandt, Dovetail Pruitt, Tamsin Greer Noa Peretz, Cyril Oaks, Ravi Odette.
I Love how Lorna Fitch web site look/ and Bartholomew Crane web site/Fazzo

```html
<!DOCTYPE html>
<html lang="en">
<head>
<meta charset="utf-8">
<title>Sunvale Bridal Atelier</title>
<link href="https://fonts.googleapis.com/css2?family=Josefin+Sans:wght@300;400;600&family=Open+Sans:wght@400;600&display=swap" rel="stylesheet">
<style>
:root{
  --blue:#1f5fb0;
  --ink:#1e1e1e;
  --body:#555;
  --band:#e4e4e4;
  --white:#fff;
  --footer:#1b1b1b;
}
*{margin:0;padding:0;box-sizing:border-box}
html,body{width:1200px;height:4215px;overflow:hidden;background:var(--white)}
body{font-family:'Josefin Sans',sans-serif;color:var(--ink);position:relative}
section,header,footer{position:absolute;left:0;width:1200px}
.abs{position:absolute}

/* header */
.site-header{top:0;height:98px;background:var(--white)}
.brand{left:98px;top:30px;display:flex;align-items:center;gap:12px;font-size:34px;font-weight:600;color:var(--blue)}
.brand-mark{width:30px;height:30px;background:var(--blue)}
.main-nav{left:450px;top:41px;width:470px;display:flex;justify-content:space-between;font-size:15px;color:var(--ink);white-space:nowrap}
.main-nav .active{color:var(--blue)}
.nav-tools{left:950px;top:28px;display:flex;gap:12px}
.tool{width:42px;height:42px;border-radius:50%;border:1.5px solid #333;display:flex;align-items:center;justify-content:center}
.tool.cart{background:var(--blue);border-color:var(--blue)}

/* hero */
.hero{top:98px;height:644px}
.hero-panel{top:0;width:600px;height:644px}
.hero-panel.groom{left:0;background:linear-gradient(110deg,#d8d8d8,#8a8a8a 45%,#2a2a2a 70%,#bdbdbd)}
.hero-panel.bride{left:600px;background:linear-gradient(250deg,#f2f2f2,#6a6a6a 40%,#1a1a1a 75%,#3a3a3a)}
.hero-title{width:600px;top:472px;text-align:center;color:var(--white);font-size:70px;font-weight:400;letter-spacing:1px;line-height:1}
.hero-link{width:600px;top:562px;text-align:center;color:var(--white);font-size:15px;font-weight:600;text-decoration:underline}

/* shared */
.section-title{font-size:62px;font-weight:400;letter-spacing:1px;line-height:1}
.copy{font-size:15px;line-height:34px;color:var(--body);font-weight:300}
.photo{display:block}
.pattern-band{background:var(--band)}

.mission{top:742px;height:655px}
.mission .section-title{left:98px;top:175px}
.mission .copy{left:98px;top:268px;width:430px}
.mission .photo{left:632px;top:95px;width:469px;height:458px;background:linear-gradient(90deg,#222 0 17%,#8a8a8a 17%,#d8d6d2 55%,#6f6f6f 83%,#222 83%)}

.atelier{top:1397px;height:598px}
.atelier .photo{left:98px;top:78px;width:534px;height:436px;background:linear-gradient(135deg,#3a3530,#7b6a55 45%,#2b2a2a 70%,#5c6670)}
.atelier .section-title{left:703px;top:124px;font-size:60px}
.atelier .subtitle{left:703px;top:192px;font-size:32px;font-weight:400;letter-spacing:1px;line-height:1}
.atelier .copy{left:703px;top:254px;width:400px}

.escapes{top:1995px;height:652px;overflow:hidden}
.escapes .photo{left:0;top:0;width:1200px;height:652px;background:linear-gradient(90deg,#fff 0,#bdbdbd 15%,#2a2a2a 35%,#111 60%,#3a3a3a 80%,#f2f2f2 100%)}
.escape-box{left:337px;top:70px;width:526px;height:481px;background:rgba(70,70,70,.82);color:var(--white);text-align:center}
.escape-box .section-title{margin-top:38px;font-size:52px;line-height:72px}
.escape-box .copy{color:#eee;margin:18px auto 0;width:440px;font-size:14px;line-height:27px}
.btn{display:inline-block;background:var(--blue);color:var(--white);font-size:15px;font-weight:600;padding:16px 24px 12px;letter-spacing:.5px}
.escape-box .btn{margin-top:18px}

.cafe{top:2647px;height:725px}
.cafe .section-title{left:98px;top:215px}
.cafe .copy{left:98px;top:304px;width:470px}
.cafe .photo{left:632px;top:96px;width:469px;height:531px;background:linear-gradient(160deg,#1a2a4a,#1d86d0 35%,#3aa8e8 55%,#123a74 80%,#0b1530)}

.products{top:3372px;height:736px;text-align:center}
.products .section-title{left:0;width:1200px;top:88px}
.products .photo{left:464px;top:183px;width:295px;height:267px;border-radius:40% 50% 20% 30%;background:radial-gradient(ellipse at 55% 60%,#c9b28a,#a89170 55%,transparent 72%)}
.arrow{top:337px;width:42px;height:51px;border:1.5px solid #777;background:#f3f3f3;display:flex;align-items:center;justify-content:center}
.arrow.prev{left:98px}.arrow.next{left:1060px}
.product-label{left:0;width:1200px;top:500px;font-size:22px;color:var(--body);font-weight:300}
.product-name{left:0;width:1200px;top:537px;font-size:27px;color:var(--ink)}
.products .btn{position:absolute;left:523px;top:587px;width:154px;padding:16px 0 12px}

.site-footer{top:4108px;height:107px;background:var(--footer);color:#ccc}
.site-footer .legal{left:98px;top:46px;font-family:'Open Sans',sans-serif;font-size:13px}
.socials{left:924px;top:34px;display:flex;gap:10px}
.socials span{width:38px;height:38px;border-radius:50%;border:1.5px solid #ccc}
</style>
</head>
<body>

<header class="site-header">
  <div class="abs brand"><span class="brand-mark"></span>Sunvale</div>
  <nav class="abs main-nav">
    <span class="active">Home</span><span>About Us</span><span>Services</span><span>Products</span><span>Team</span><span>Contact Us</span>
  </nav>
  <div class="abs nav-tools">
    <span class="tool"><svg width="16" height="16" viewBox="0 0 16 16"><circle cx="7" cy="7" r="5" fill="none" stroke="#222" stroke-width="2"/><line x1="11" y1="11" x2="15" y2="15" stroke="#222" stroke-width="2"/></svg></span>
    <span class="tool"><svg width="14" height="16" viewBox="0 0 14 16"><circle cx="7" cy="4.5" r="3.5" fill="#222"/><path d="M0 16a7 6 0 0 1 14 0z" fill="#222"/></svg></span>
    <span class="tool cart"><svg width="18" height="16" viewBox="0 0 18 16"><path d="M1 1h3l2 9h9l2-7H5" fill="none" stroke="#fff" stroke-width="2"/><circle cx="7" cy="14" r="1.6" fill="#fff"/><circle cx="14" cy="14" r="1.6" fill="#fff"/></svg></span>
  </div>
</header>

<section class="hero">
  <div class="abs hero-panel groom" role="img" aria-label="Black and white portrait of a groom in a tuxedo">
    <h2 class="abs hero-title">GROOM</h2>
    <a class="abs hero-link">SHOP NEW ARRIVALS</a>
  </div>
  <div class="abs hero-panel bride" role="img" aria-label="Black and white portrait of a bride in a flowing gown">
    <h2 class="abs hero-title">BRIDE</h2>
    <a class="abs hero-link">SHOP NEW ARRIVALS</a>
  </div>
</section>

<section class="mission">
  <h2 class="abs section-title">OUR MISSION</h2>
  <p class="abs copy">To open a one stop shop for the bride &amp; groom to make everything simple for the bride at this stressful time in her life to take a lot of the burden of the bride for she can enjoy the processed of getting marry. The bride will be assign a consultant that will keep in touch with her for 24 months, for the wedding and the first year anniversary.</p>
  <div class="abs photo" role="img" aria-label="Bridal boutique interior with gowns on display"></div>
</section>

<section class="atelier pattern-band">
  <div class="abs photo" role="img" aria-label="Classic film still of a woman in sunglasses and pearls"></div>
  <h2 class="abs section-title">SUNVALE</h2>
  <h3 class="abs subtitle">BRIDAL ATELIER</h3>
  <p class="abs copy">will sell bridal gowns, jewelry, shoes party favors. If she has a wedding gown -that she loves we will find a way to make that dream come true and make the bride feel confident and happy through the process. Flower girls, bridesmaids, mother of the bride. And tuxedo rental for the groom with a cigar room….</p>
</section>

<section class="escapes">
  <div class="abs photo" role="img" aria-label="Black and white photo of a couple embracing"></div>
  <div class="abs escape-box">
    <h2 class="section-title">WAYFARER<br>ESCAPES GLOBAL<br>&amp; CO</h2>
    <p class="copy">is another part of the company the one stop shop experience that we will be offering the couples a travel agency &amp; wedding consultant. If the couple is looking to do a destination wedding or honeymoon destination we can make the plans and work with the resort by confence call.</p>
    <a class="btn">READ MORE</a>
  </div>
</section>

<section class="cafe">
  <h2 class="abs section-title">CAFÉ DES PINS</h2>
  <p class="abs copy">will create a unique restaurant where the bride and wedding party can sit and eat after their fitting for the dresses, featuring Chef Tarik creation and offering catering. Cake testing from different bakery, wine, coffee specialties drinks, a romantic restantant for couple at night time feature cigar room, wine bar party room.</p>
  <div class="abs photo" role="img" aria-label="Blue decorated cakes and candles on a dessert table"></div>
</section>

<section class="products pattern-band">
  <h2 class="abs section-title">PRODUCT</h2>
  <div class="abs photo" role="img" aria-label="Gold embellished high heel bridal shoe"></div>
  <span class="abs arrow prev"><svg width="12" height="18" viewBox="0 0 12 18"><path d="M10 1 2 9l8 8" fill="none" stroke="#555" stroke-width="2"/></svg></span>
  <span class="abs arrow next"><svg width="12" height="18" viewBox="0 0 12 18"><path d="M2 1l8 8-8 8" fill="none" stroke="#555" stroke-width="2"/></svg></span>
  <p class="abs product-label">Bride Sandals</p>
  <p class="abs product-name">Nemo enim ipsam voluptatem quia voluptas sit asper</p>
  <a class="btn">VIEW DETAILS</a>
</section>

<footer class="site-footer">
  <p class="abs legal">Copyrights © 2018, Sunvale Bridal Atelier. All rights reserved.</p>
  <div class="abs socials"><span></span><span></span><span></span><span></span></div>
</footer>

</body>
</html>
```